Job Recruiting Agemcy

almost like my current site www.plorvex.com but with these changes see and what i meant about the across the to the site says home job companies categories pages blog and login sign up that should only be the 4 i said only 1 home 2 industries 3 jobs 4 contact us. and remove latest blog post and our partners because that's not us we have to post acuarte information thanks and the name of the company if your using is is work and careful hiring partners and want it easy for us to post and remove jobs and where it emails us every resume or person that applies

Requirements
Must have
• must send email to us when an application is submitted and try to incorparate the colors of current site
Nice to have
• i want a pretty basic site for now just like the one i have but with all thats above were its easy for me being the own to be able to post jobs and everything

```html
<!DOCTYPE html>
<html lang="en">
<head>
<meta charset="utf-8">
<title>Plorvex — Work and Careful Hiring Partners</title>
<link rel="stylesheet" href="https://fonts.googleapis.com/css2?family=Exo+2:wght@400;500;600;700&display=swap">
<style>
:root{
  --purple:#6410d6;
  --violet:#7a1fb8;
  --plum:#561a5c;
  --deep:#4a1555;
  --rose:#c0466a;
  --coral:#e0505a;
  --ink:#2b2b2b;
  --muted:#444;
  --line:#e4d6f2;
}
*{box-sizing:border-box;margin:0;padding:0}
html,body{width:1200px;height:3405px;overflow:hidden}
body{position:relative;background:#fff;font-family:"Exo 2",sans-serif;color:var(--ink)}
.abs{position:absolute}
.hero-bg{left:0;top:0;width:1200px;height:860px;background:linear-gradient(90deg,#ecdcd4 0%,#e6d4ca 55%,#d9c3b6 100%)}
.hero-photo{left:560px;top:90px;width:640px;height:770px;background:radial-gradient(ellipse at 55% 45%,#c9a58f 0%,#d8c0b2 45%,rgba(230,212,202,0) 75%)}
.brand{font-weight:700;color:var(--purple);letter-spacing:1px;white-space:nowrap}
.brand-top{left:130px;top:135px;font-size:30px}
.tagline{font-size:8px;font-weight:600;color:#222;letter-spacing:.5px}
.nav{left:543px;top:61px;font-size:16px;color:#222}
.nav a{position:absolute;white-space:nowrap;text-decoration:none;color:#222}
.btn{display:flex;align-items:center;justify-content:center;border-radius:20px;color:#fff;font-size:16px;background:var(--purple);white-space:nowrap}
.btn-login{left:908px;top:53px;width:87px;height:36px}
.btn-signup{left:1002px;top:53px;width:87px;height:36px;background:var(--violet)}
.hero-kicker{left:119px;top:328px;font-size:32px;color:var(--rose);white-space:nowrap}
.hero-title{left:119px;top:368px;font-size:52px;font-weight:700;color:var(--deep);white-space:nowrap}
.field{top:445px;width:260px;height:51px;border-radius:26px;background:#fff;display:flex;align-items:center;padding-left:22px;gap:12px;font-size:14px;font-weight:600;color:#222}
.field-key{left:110px}
.field-loc{left:394px}
.btn-search{left:666px;top:445px;width:175px;height:51px;border-radius:26px;background:linear-gradient(90deg,#4a0fb8,#7a1fa0);color:#fff;font-size:22px;font-weight:700;display:flex;align-items:center;justify-content:center}
.dots{left:571px;top:633px;display:flex;gap:6px}
.dots span{width:26px;height:5px;background:var(--coral)}
.dots span+span{width:10px;background:var(--purple)}
.wave{left:0;top:0}
.brand-mid{left:0;width:1200px;top:855px;text-align:center;font-size:30px}
.brand-mid .tagline{display:block;margin-top:2px}
.intro{left:0;width:1200px;top:932px;text-align:center;font-size:24px;line-height:41px;color:var(--muted);white-space:nowrap}
.section-title{left:0;width:1200px;text-align:center;font-weight:700}
.industries-title{top:1080px;font-size:42px;color:#6a14d8}
.industry{width:441px;height:102px;border:1px solid var(--line);border-radius:24px;background:#fff;box-shadow:0 5px 8px rgba(120,60,200,.15);display:flex;align-items:center;overflow:hidden}
.industry p{flex:1;padding-left:40px;font-size:19px;line-height:23px;color:#333;white-space:nowrap}
.industry .tab{width:57px;height:100%;background:var(--purple);display:flex;align-items:center;justify-content:center}
.recent-band{left:0;top:1528px;width:1200px;height:105px;background:var(--plum)}
.recent-notch{left:584px;top:1632px;width:0;height:0;border-left:16px solid transparent;border-right:16px solid transparent;border-top:12px solid var(--plum)}
.recent-title{top:1548px;font-size:42px;color:#fff}
.job{left:119px;width:962px;height:104px;border:1px solid var(--line);border-radius:30px;background:#fff;box-shadow:0 5px 8px rgba(120,60,200,.15)}
.job h3{position:absolute;left:70px;top:22px;font-size:22px;font-weight:600;color:#222}
.job p{position:absolute;left:70px;top:58px;font-size:13px;color:#333;white-space:nowrap}
.job .apply{position:absolute;left:786px;top:32px;width:115px;height:34px;font-size:16px;background:var(--violet)}
.testimonials{left:0;top:2487px;width:1200px;height:582px;background:linear-gradient(110deg,#6a1fd0 0%,#5a22b8 45%,#7a2ab0 80%,#8a2e98 100%)}
.testi-title{top:2533px;font-size:42px;color:#fff}
.avatar{width:94px;height:94px;border-radius:50%;background:#e9dff2;border:5px solid #3a1a6a}
.quote{width:400px;text-align:center;color:#fff;font-size:16px;line-height:26px;white-space:nowrap}
.quote .who{position:absolute;left:0;width:400px;top:124px;font-weight:700;font-size:16px}
.btn-more{left:543px;top:2979px;width:114px;height:34px;background:var(--coral);font-size:16px}
.foot-brand{left:145px;top:3268px;font-size:30px}
.foot-head{top:3130px;font-size:32px;font-weight:700;color:#6a18c8;white-space:nowrap}
.foot-item{font-size:16px;color:#333;line-height:26px;white-space:nowrap}
.social{width:28px;height:28px;border-radius:50%;border:3px solid #111}
.copy{left:858px;top:3365px;font-size:14px;color:#222;white-space:nowrap}
</style>
</head>
<body>
<div class="abs hero-bg"></div>
<div class="abs hero-photo" role="img" aria-label="Photo of a smiling woman in glasses holding a tablet"></div>

<div class="abs brand brand-top">PLORVEX<div class="tagline">SERVICING YOU SINCE 1980</div></div>

<nav class="abs nav">
  <a href="#" style="left:0">Home</a>
  <a href="#" style="left:72px">Industries</a>
  <a href="#" style="left:180px">Jobs</a>
  <a href="#" style="left:249px">Contact us</a>
</nav>
<a class="abs btn btn-login">Login</a>
<a class="abs btn btn-signup">Sign Up</a>

<div class="abs hero-kicker">Search from 0 job offers</div>
<h1 class="abs hero-title">Your career starts here!</h1>
<div class="abs field field-key">
  <svg width="14" height="14" viewBox="0 0 14 14"><circle cx="6" cy="6" r="4.5" fill="none" stroke="#666" stroke-width="1.4"/><line x1="9.3" y1="9.3" x2="13" y2="13" stroke="#666" stroke-width="1.4"/></svg>Key words</div>
<div class="abs field field-loc">
  <svg width="12" height="15" viewBox="0 0 12 15"><path d="M6 14C3 10 1 7.5 1 5.5a5 5 0 0 1 10 0C11 7.5 9 10 6 14z" fill="none" stroke="#666" stroke-width="1.3"/><circle cx="6" cy="5.5" r="1.6" fill="none" stroke="#666" stroke-width="1.2"/></svg>Location</div>
<div class="abs btn-search">Search</div>
<div class="abs dots"><span></span><span></span><span></span></div>

<svg class="abs wave" width="1200" height="900" viewBox="0 0 1200 900">
  <path d="M0 767 C150 712 290 687 420 687 C700 687 1000 735 1200 770 L1200 900 L0 900Z" fill="#6410d6"/>
  <path d="M0 846 C150 765 300 697 430 697 C700 697 1000 760 1200 806 L1200 900 L0 900Z" fill="#fff"/>
</svg>

<div class="abs brand brand-mid">PLORVEX<span class="tagline">SERVICING YOU SINCE 1980</span></div>

<p class="abs intro">We have over 35 years of Specialized Recruiting and souring experience. We<br>cover a broad spectrum of industries to include some of the top aerospace<br>and pharmaceutical commercial companies of today.</p>

<h2 class="abs section-title industries-title">Industries we support</h2>

<div class="abs industry" style="left:143px;top:1180px"><p>Aero Space- Orvane Aero Space<br>Controls, Stellaro Voltmere Electric</p><span class="tab"><svg width="10" height="14" viewBox="0 0 10 14"><path d="M2 2l5 5-5 5" fill="none" stroke="#fff" stroke-width="2.4"/></svg></span></div>
<div class="abs industry" style="left:616px;top:1180px"><p>Pharmaceutical/ Biotechnology<br>Quenlio Tech , Morvannel cosmetics</p><span class="tab"><svg width="10" height="14" viewBox="0 0 10 14"><path d="M2 2l5 5-5 5" fill="none" stroke="#fff" stroke-width="2.4"/></svg></span></div>
<div class="abs industry" style="left:143px;top:1318px"><p>Transportation- Brannock Trucking,<br>Zelqo Freight</p><span class="tab"><svg width="10" height="14" viewBox="0 0 10 14"><path d="M2 2l5 5-5 5" fill="none" stroke="#fff" stroke-width="2.4"/></svg></span></div>
<div class="abs industry" style="left:616px;top:1318px"><p style="align-self:flex-start;padding-top:28px">Medical - Medquova, Trelvanix</p><span class="tab"><svg width="10" height="14" viewBox="0 0 10 14"><path d="M2 2l5 5-5 5" fill="none" stroke="#fff" stroke-width="2.4"/></svg></span></div>

<div class="abs recent-band"></div>
<div class="abs recent-notch"></div>
<h2 class="abs section-title recent-title">Recent Jobs</h2>

<div class="abs job" style="top:1701px"><h3>Lorium ipsum Dolor Amit</h3><p>Neque porro quisquam est qui dolorem ipsum quia dolor sit amet, consectetur, adipisci velit...</p><a class="btn apply">Apply Now</a></div>
<div class="abs job" style="top:1840px"><h3>Lorium ipsum Dolor Amit</h3><p>Neque porro quisquam est qui dolorem ipsum quia dolor sit amet, consectetur, adipisci velit...</p><a class="btn apply">Apply Now</a></div>
<div class="abs job" style="top:1978px"><h3>Lorium ipsum Dolor Amit</h3><p>Neque porro quisquam est qui dolorem ipsum quia dolor sit amet, consectetur, adipisci velit...</p><a class="btn apply">Apply Now</a></div>
<div class="abs job" style="top:2117px"><h3>Lorium ipsum Dolor Amit</h3><p>Neque porro quisquam est qui dolorem ipsum quia dolor sit amet, consectetur, adipisci velit...</p><a class="btn apply">Apply Now</a></div>
<div class="abs job" style="top:2256px"><h3>Lorium ipsum Dolor Amit</h3><p>Neque porro quisquam est qui dolorem ipsum quia dolor sit amet, consectetur, adipisci velit...</p><a class="btn apply">Apply Now</a></div>

<svg class="abs" style="left:584px;top:2400px" width="32" height="34" viewBox="0 0 32 34"><path d="M16 2v28M4 19l12 12 12-12" fill="none" stroke="#7a1fb8" stroke-width="4"/></svg>

<div class="abs testimonials" role="img" aria-label="Photo of colleagues working together at a table, tinted purple"></div>
<h2 class="abs section-title testi-title">Testimonials</h2>
<div class="abs avatar" style="left:313px;top:2656px" role="img" aria-label="Client portrait"></div>
<div class="abs avatar" style="left:793px;top:2656px" role="img" aria-label="Client portrait"></div>
<p class="abs quote" style="left:160px;top:2766px">Thanks for the great service. Quillomar has<br>completely surpassed our expectations. Quillomar is<br>the most valuable business resource we have ever<br>purchased.<span class="who">Marcus Dale Brand Manager in Brindlemark Inc.</span></p>
<p class="abs quote" style="left:640px;top:2766px">I just can't get enough of Quillomar. I want to get a<br>T-Shirt with Quillomar on it so I can show it off to<br>everyone. This is simply unbelievable!<span class="who">Tobias Reed Key Account Manager in Chirvella Inc.</span></p>
<svg class="abs" style="left:108px;top:2760px" width="22" height="30" viewBox="0 0 22 30"><path d="M17 3L5 15l12 12" fill="none" stroke="#fff" stroke-width="5"/></svg>
<svg class="abs" style="left:1075px;top:2760px" width="22" height="30" viewBox="0 0 22 30"><path d="M5 3l12 12L5 27" fill="none" stroke="#fff" stroke-width="5"/></svg>
<a class="abs btn btn-more">Read more</a>

<div class="abs brand foot-brand">PLORVEX<div class="tagline">SERVICING YOU SINCE 1980</div></div>

<h3 class="abs foot-head" style="left:396px">Contact Us</h3>
<svg class="abs" style="left:394px;top:3206px" width="12" height="16" viewBox="0 0 12 16"><path d="M6 15C3 11 1 8 1 6a5 5 0 0 1 10 0c0 2-2 5-5 9z" fill="#111"/><circle cx="6" cy="6" r="1.8" fill="#fff"/></svg>
<p class="abs foot-item" style="left:432px;top:3201px">#123 Lorium ipsum<br>Dolor amit,</p>
<svg class="abs" style="left:394px;top:3286px" width="15" height="15" viewBox="0 0 15 15"><path d="M3 1l3 3-1.5 2a8 8 0 0 0 4.5 4.5L11 9l3 3-2 2C6 14 1 9 1 3z" fill="#111"/></svg>
<p class="abs foot-item" style="left:432px;top:3279px">1-800 555 0142</p>
<svg class="abs" style="left:394px;top:3312px" width="16" height="12" viewBox="0 0 16 12"><rect x="0" y="0" width="16" height="12" fill="#111"/><path d="M0 1l8 6 8-6" fill="none" stroke="#fff" stroke-width="1.2"/></svg>
<p class="abs foot-item" style="left:432px;top:3304px">info@plorvex.com</p>

<h3 class="abs foot-head" style="left:650px">Quick Links</h3>
<div class="abs" style="left:652px;top:3201px">
  <p class="foot-item" style="padding-left:38px;position:relative">Home<br>Industries<br>Jobs<br>Contact Us</p>
  <svg class="abs" style="left:0;top:0" width="10" height="104" viewBox="0 0 10 104"><g fill="none" stroke="#111" stroke-width="2"><path d="M3 9l4 4-4 4"/><path d="M3 35l4 4-4 4"/><path d="M3 61l4 4-4 4"/><path d="M3 87l4 4-4 4"/></g></svg>
</div>

<h3 class="abs foot-head" style="left:912px">Follow Us</h3>
<div class="abs social" style="left:916px;top:3206px" role="img" aria-label="Social profile"></div>
<div class="abs social" style="left:976px;top:3206px" role="img" aria-label="Social profile"></div>
<div class="abs social" style="left:1035px;top:3206px" role="img" aria-label="Social profile"></div>

<p class="abs copy">© 2020 &nbsp;|&nbsp; www.plorvex.com</p>
</body>
</html>
```